Food Trade Show Advertisement

One full-page advertisement sent as a high-resolution .pdf file that is 11.125" w x 14.25" h

Details on the the wording and pictures will be provided
The to include:
Company logo, product photos (to be supplied), wording (to be supplied), Booth number (to be supplied)
Colors - hot pink
Attached is the guidelines for the advertisement

```html
<!DOCTYPE html>
<html lang="en">
<head>
<meta charset="utf-8">
<title>Trade Show Advertisement</title>
<link href="https://fonts.googleapis.com/css2?family=Bebas+Neue&family=Poppins:wght@400;600;700;800&display=swap" rel="stylesheet">
<style>
  :root {
    --berry: #b51e5a;
    --hot-pink: #ff63ad;
    --maroon: #6e0530;
    --white: #ffffff;
    --brand-green: #2fe03a;
    --booth-green: #00f500;
    --booth-text: #0b3d0b;
    --ink: #000000;
  }
  * { margin: 0; padding: 0; box-sizing: border-box; }
  html, body { width: 931px; height: 1200px; overflow: hidden; background: var(--white); }
  .ad {
    position: relative; width: 931px; height: 1200px; overflow: hidden;
    background: var(--berry); font-family: "Poppins", sans-serif; color: var(--white);
  }
  .ad > * { position: absolute; }
  .dashed-frame {
    left: 18px; top: 18px; width: 895px; height: 1060px;
    border: 1.5px dashed rgba(255,255,255,0.85); border-radius: 12px;
  }
  .brand-name {
    left: 0; width: 931px; top: 130px; text-align: center;
    font-weight: 800; font-size: 19px; line-height: 24px; letter-spacing: 2.5px; color: var(--brand-green);
  }
  .headline {
    left: 0; width: 931px; top: 155px; text-align: center;
    font-weight: 800; font-size: 46px; letter-spacing: -0.5px; line-height: 54px;
  }
  .tagline-band {
    left: 226px; top: 212px; width: 474px; height: 60px;
    background: var(--hot-pink);
    clip-path: polygon(4% 12%, 30% 4%, 62% 0, 98% 8%, 96% 40%, 100% 70%, 92% 96%, 55% 100%, 20% 94%, 0 100%, 3% 66%, 0 40%);
  }
  .tagline {
    left: 226px; width: 474px; top: 221px; text-align: center;
    font-weight: 700; font-size: 29px; line-height: 40px;
  }
  .stat-number {
    left: 119px; top: 314px; width: 222px; height: 65px; border-radius: 8px;
    background: var(--maroon); text-align: center;
    font-weight: 800; font-size: 52px; line-height: 68px;
  }
  .stat-label {
    left: 346px; top: 314px; width: 464px; height: 65px; border-radius: 8px;
    background: var(--white); color: var(--hot-pink); text-align: center;
    font-family: "Bebas Neue", sans-serif; font-size: 60px; line-height: 70px;
  }
  .event-year {
    left: 40px; top: 556px; transform-origin: 0 0; transform: rotate(-90deg);
    width: 142px; text-align: center;
    font-weight: 800; font-size: 52px; line-height: 52px; color: var(--hot-pink);
  }
  .event-name {
    left: 100px; top: 403px; font-weight: 700; font-size: 90px; line-height: 73px; letter-spacing: -2px;
  }
  .event-divider { left: 426px; top: 415px; width: 3px; height: 138px; background: var(--maroon); }
  .event-date {
    left: 446px; top: 405px; font-weight: 700; font-size: 76px; line-height: 73px; letter-spacing: -2px;
  }
  .event-date .month { color: var(--hot-pink); }
  .event-time {
    left: 640px; width: 280px; top: 408px; text-align: center;
    font-weight: 700; font-size: 46px; line-height: 56px;
  }
  .time-joiner {
    display: block; width: 38px; height: 38px; margin: -8px auto -6px; border-radius: 50%;
    background: var(--hot-pink); font-size: 16px; line-height: 38px; font-weight: 700;
  }
  .venue { left: 42px; top: 588px; display: flex; gap: 14px; align-items: flex-start; }
  .venue-text { font-weight: 700; font-size: 22px; line-height: 25px; text-transform: uppercase; }
  .product-photo { left: 0; top: 0; width: 931px; height: 1200px; }
  .offer { left: 44px; top: 652px; font-size: 27px; line-height: 34px; }
  .offer .lead { color: var(--hot-pink); }
  .offer strong { font-weight: 700; }
  .offer .accent { color: var(--hot-pink); font-weight: 700; }
  .booth {
    left: 284px; top: 637px; width: 204px; height: 204px; border-radius: 50%;
    background: var(--booth-green); border: 3px solid #123a46;
    text-align: center; color: var(--booth-text);
    padding-top: 44px; font-weight: 800; font-size: 21px; line-height: 27px;
  }
  .booth .booth-number { display: block; color: var(--maroon); font-size: 50px; line-height: 54px; }
  .product-line { left: 44px; top: 934px; font-weight: 800; font-size: 40px; line-height: 50px; color: var(--white); }
  .contact-heading { left: 40px; top: 1030px; font-weight: 700; font-size: 34px; line-height: 44px; color: var(--hot-pink); }
  .contact-band { left: 0; top: 1077px; width: 931px; height: 123px; background: var(--ink); }
  .contact-list { left: 50px; top: 1088px; list-style: none; font-size: 17px; line-height: 25px; }
  .contact-list li { display: flex; align-items: center; gap: 10px; }
  .contact-list svg { width: 13px; height: 13px; flex: none; }
</style>
</head>
<body>
<main class="ad">
  <div class="dashed-frame"></div>

  <div class="brand-name">MEADOWRISE</div>
  <h1 class="headline">SUSTAINABLE INGREDIENTS</h1>
  <div class="tagline-band"></div>
  <p class="tagline">Direct from the Farm</p>

  <div class="stat-number">50,000</div>
  <div class="stat-label">ACRESS OF EXPERIENCE</div>

  <div class="event-year">2023</div>
  <h2 class="event-name">TRADE<br>SHOW</h2>
  <div class="event-divider"></div>
  <div class="event-date">25TH<br><span class="month">JUNE</span></div>
  <div class="event-time">6.30 PM<span class="time-joiner">TO</span>8.30PM</div>

  <div class="venue">
    <svg width="30" height="40" viewBox="0 0 28 38" aria-hidden="true">
      <ellipse cx="14" cy="34" rx="12" ry="3.5" fill="#1a1a1a"/>
      <path d="M14 1C7 1 2 6 2 12.5 2 21 14 33 14 33S26 21 26 12.5C26 6 21 1 14 1Z" fill="#1a1a1a"/>
      <circle cx="14" cy="12.5" r="5" fill="#b51e5a"/>
    </svg>
    <p class="venue-text">22-480 Prairie Lane, Saskatoon<br>Saskatchewan, Canada</p>
  </div>

  <div class="contact-band"></div>

  <svg class="product-photo" viewBox="0 0 931 1200" role="img" aria-label="Product photo: white bowls of red lentils, a spoon of roasted chickpeas and a bowl of green peas on a light table with fresh parsley">
    <defs>
      <radialGradient id="table-tone" cx="0.55" cy="0.6" r="0.7">
        <stop offset="0" stop-color="#f4f5f7"/>
        <stop offset="0.55" stop-color="#e6e9ee"/>
        <stop offset="1" stop-color="#d3d8df"/>
      </radialGradient>
    </defs>
    <circle cx="710" cy="955" r="385" fill="url(#table-tone)" stroke="#000" stroke-width="6"/>
  </svg>

  <p class="offer">
    <span class="lead">We produce</span><br>
    Protein, Fiber,<br>
    Flour &amp; Starch<br>
    <strong>for Aquaculture,<br>Feed, Pet Food<br>&amp; </strong><span class="accent">Human<br>Consumption</span>
  </p>

  <div class="booth">VISIT US AT<br>BOOTH NO<span class="booth-number">100</span></div>

  <div class="product-line">Brightpulse</div>

  <h3 class="contact-heading">CONTACT US</h3>
  <ul class="contact-list">
    <li>
      <svg viewBox="0 0 16 16" aria-hidden="true"><path d="M3 1l3 3-1.5 2c1 2 3 4 5 5L11.5 9.5l3 3-2 2.5C7 14.5 1.5 9 1 3.5Z" fill="#ff63ad"/></svg>
      1-306-555-0142
    </li>
    <li>
      <svg viewBox="0 0 16 16" aria-hidden="true"><rect x="1" y="3" width="14" height="10" rx="1.5" fill="#ff63ad"/><path d="M1.5 4 8 9l6.5-5" stroke="#000" stroke-width="1.4" fill="none"/></svg>
      info@meadowrisefoods.com
    </li>
    <li>
      <svg viewBox="0 0 16 16" aria-hidden="true"><circle cx="8" cy="8" r="7" fill="#ff63ad"/><path d="M1 8h14M8 1c-3 3.5-3 10.5 0 14M8 1c3 3.5 3 10.5 0 14M2.5 4.5h11M2.5 11.5h11" stroke="#000" stroke-width="1" fill="none"/></svg>
      www.meadowrisefoods.com
    </li>
  </ul>
</main>
</body>
</html>
```